Small corporate website template design

I need a couple templates designed for a small corporate website. The corporate site reflects the existence of the parent company which will own various brands/services that have their own websites, so it will mainly be used to present who we are, what we do, what is happening (news/events), how to contact us, link off to our other brand/service sites, as well as post information for public relations, investors, and job opportunities.

The company name is Brelvanto LLC (www.brelvanto-example.com), and the name is representative of stratified layers of interconnected digital services. The corporate site is not expected to generate a bunch of fanfare - that honor will be reserved for the externally linked brand/service sites.

The provided logo may be manipulated in color, size, shape, positioning, etc. to get it to fit with the design, but should be integrated in some way.

What we are looking for is a home page layout as well as a template for an inner page whereby the navigation/logo, etc may be diminished to some extent for the inner pages. We are also interested in reusable elements such as dividers, content containers, etc. in order to represent the types of information described above that we would like to present as described above.

We are particularly interested in consistency of design elements, conservative use of color (including consideration of accessibility concerns), judicious use of whitespace in favor of simplified messaging, and something lending itself well to internationalization/translation.

Target Market(s)

Small business owners, entrepreneurs (B2B)

Number of Pages Required

2 page

Font styles to use
Sans Serif

Requirements
Must have
• See the attached PDF with the logo concept, color swatches, and comparative sites.

```html
<!DOCTYPE html>
<html lang="en">
<head>
<meta charset="utf-8">
<title>Brelvanto LLC</title>
<link rel="stylesheet" href="https://fonts.googleapis.com/css2?family=Ubuntu:wght@400;500&family=Arimo:wght@400;700&display=swap">
<style>
:root{
  --orange:#ff9800;
  --orange-deep:#f28c00;
  --ink:#2b2b2b;
  --body:#555555;
  --grey-band:#ebebeb;
  --white:#ffffff;
  --hero-overlay:rgba(30,30,30,.72);
}
*{box-sizing:border-box;margin:0;padding:0}
html,body{width:1200px;height:3066px;overflow:hidden}
body{font-family:"Arimo",Arial,sans-serif;color:var(--body);background:var(--white);position:relative}
.display{font-family:"Ubuntu","Trebuchet MS",sans-serif;font-weight:400}
.accent{color:var(--orange)}
a{color:inherit;text-decoration:none}
section,header,footer,nav{position:absolute;left:0;width:1200px}

/* top bar */
.topbar{top:0;height:123px}
.topbar .contact{position:absolute;top:48px;display:flex;align-items:center;gap:14px;font-size:15px;color:#444}
.topbar .phone{left:78px}
.topbar .mail{right:80px}
.brand{position:absolute;left:0;right:0;top:38px;display:flex;justify-content:center;align-items:center;gap:12px}
.brand .dot{width:34px;height:34px;border-radius:50%;background:var(--orange)}
.brand .name{font-family:"Ubuntu",sans-serif;font-size:28px;font-weight:500;color:var(--orange)}

/* nav */
.mainnav{top:123px;height:57px;background:var(--orange)}
.mainnav a{position:absolute;top:19px;font-size:15px;color:var(--white);transform:translateX(-50%);white-space:nowrap}

/* hero */
.hero{top:180px;height:625px}
.hero .photo{position:absolute;inset:0;background:linear-gradient(100deg,#3a3633 0%,#8d8680 35%,#d9d4ce 60%,#bdb8b2 80%,#6d6a66 100%)}
.hero .panel{position:absolute;left:0;top:198px;width:521px;height:231px;background:var(--hero-overlay)}
.hero h1{position:absolute;left:80px;top:222px;font-size:45px;line-height:53px;color:var(--white);font-weight:500}
.btn{display:inline-block;background:var(--orange);color:var(--white);border-radius:26px;font-size:17px;text-align:center;text-transform:uppercase}
.hero .btn{position:absolute;left:78px;top:347px;width:157px;height:50px;line-height:50px}

/* welcome */
.welcome{top:805px;height:405px;text-align:center}
.section-title{font-size:42px;color:var(--ink)}
.welcome .section-title{margin-top:60px}
.welcome p{width:560px;margin:28px auto 0;font-size:15px;line-height:26px}
.welcome .btn{margin-top:36px;width:156px;height:52px;line-height:52px;box-shadow:0 4px 6px rgba(0,0,0,.25)}

/* services */
.services{top:1210px;height:448px;background:var(--grey-band);text-align:center}
.services .section-title{margin-top:56px}
.service{position:absolute;top:135px;width:300px;transform:translateX(-50%)}
.service .icon{width:94px;height:94px;margin:0 auto;border:2px solid var(--orange);display:flex;align-items:center;justify-content:center}
.service .icon.filled{background:var(--orange)}
.service h3{margin-top:20px;font-size:16px;font-weight:400;color:var(--orange)}
.service p{margin-top:12px;font-size:15px;line-height:26px}
.readmore{display:inline-block;margin-top:6px;font-size:14px;color:var(--orange);text-decoration:underline}

/* news */
.news{top:1658px;height:636px;text-align:center}
.news .section-title{margin-top:54px}
.news .intro{width:660px;margin:22px auto 0;font-size:15px;line-height:26px}
.post{position:absolute;top:216px;width:323px;text-align:left}
.post .thumb{position:relative;height:209px}
.post .date{position:absolute;left:0;bottom:0;width:46px;height:60px;background:var(--orange);color:var(--white);text-align:center;padding-top:6px}
.post .date b{display:block;font-family:"Ubuntu",sans-serif;font-size:27px;font-weight:400;line-height:28px}
.post .date span{font-size:14px}
.post h3{margin-top:20px;font-size:16px;font-weight:400;color:var(--orange)}
.post p{margin-top:10px;font-size:15px;line-height:26px}
.post .readmore{margin-top:4px}

/* newsletter */
.newsletter{top:2294px;height:135px;background:var(--orange)}
.newsletter h2{position:absolute;left:108px;top:42px;font-size:40px;color:var(--white)}
.newsletter .field{position:absolute;left:675px;top:41px;width:415px;height:51px;border:2px solid var(--white);border-radius:26px;color:var(--white);font-size:14px;padding:15px 0 0 22px}
.newsletter .submit{position:absolute;right:-2px;top:-2px;width:137px;height:51px;border-radius:26px;background:var(--white);color:var(--orange);font-size:17px;text-align:center;line-height:51px}

/* testimonial */
.testimonial{top:2429px;height:261px;background:var(--grey-band)}
.testimonial h2{position:absolute;left:82px;top:60px;font-size:41px;line-height:56px;color:var(--ink)}
.testimonial .rule{position:absolute;left:296px;top:28px;width:2px;height:190px;background:var(--orange)}
.testimonial .avatar{position:absolute;left:327px;top:61px;width:104px;height:106px;background:linear-gradient(160deg,#d8d3cf,#6a5f5a)}
.testimonial blockquote{position:absolute;left:456px;top:62px;width:620px;font-size:15px;line-height:27px}
.testimonial cite{position:absolute;left:456px;top:148px;font-style:normal;font-size:14px;color:var(--orange)}
.dots{position:absolute;left:540px;top:213px;display:flex;gap:9px}
.dots i{width:17px;height:17px;border-radius:50%;border:2px solid var(--orange)}
.dots i.on{background:var(--orange)}

/* contact */
.contact-strip{top:2690px;height:167px}
.contact-item{position:absolute;top:50px;width:330px;padding-left:42px}
.contact-item svg{position:absolute;left:0;top:2px}
.contact-item h4{font-size:17px;font-weight:400;color:var(--orange);text-transform:uppercase}
.contact-item p{margin-top:10px;font-size:15px;line-height:27px}

/* footer */
.site-footer{top:2857px;height:209px;background:var(--orange);color:var(--white);text-align:center}
.footer-links{margin-top:42px;font-size:15px}
.footer-links span{margin:0 20px}
.social{margin-top:30px;display:flex;justify-content:center;gap:20px}
.social i{width:41px;height:41px;border-radius:50%;background:var(--white)}
.site-footer hr{position:absolute;left:78px;top:157px;width:1044px;border:0;border-top:1px solid rgba(255,255,255,.8)}
.copyright{position:absolute;left:0;right:0;top:174px;font-size:14px}
</style>
</head>
<body>

<header class="topbar">
  <div class="contact phone">
    <svg width="18" height="18" viewBox="0 0 24 24"><path fill="#ff9800" d="M6.6 10.8a15.1 15.1 0 0 0 6.6 6.6l2.2-2.2c.3-.3.7-.4 1-.2 1.1.4 2.3.6 3.6.6.6 0 1 .4 1 1V20c0 .6-.4 1-1 1A17 17 0 0 1 3 4c0-.6.4-1 1-1h3.5c.6 0 1 .4 1 1 0 1.3.2 2.5.6 3.6.1.3 0 .7-.2 1z"/></svg>
    <span>123 456 7890</span>
  </div>
  <div class="brand"><span class="dot"></span><span class="name">Brelvanto LLC</span></div>
  <div class="contact mail">
    <svg width="20" height="15" viewBox="0 0 20 15"><rect width="20" height="15" fill="#ff9800"/><path d="M1 1l9 7 9-7" stroke="#fff" stroke-width="1.6" fill="none"/></svg>
    <span>info@brelvanto-example.com</span>
  </div>
</header>

<nav class="mainnav">
  <a href="#" style="left:348px">Home</a>
  <a href="#" style="left:466px">About Us</a>
  <a href="#" style="left:595px">Services</a>
  <a href="#" style="left:709px">News</a>
  <a href="#" style="left:834px">Contact Us</a>
</nav>

<section class="hero">
  <div class="photo" role="img" aria-label="Team of colleagues gathered around a laptop in a bright office"></div>
  <div class="panel"></div>
  <h1 class="display">Welcome To<br>Brelvanto LLC</h1>
  <a class="btn" href="#">Contact Us</a>
</section>

<section class="welcome">
  <h2 class="section-title display">Welcome To <span class="accent">Brelvanto LLC</span></h2>
  <p>Lorem Ipsum is simply dummy text of the printing and typesetting industry. Lorem Ipsum has been the industry's standard dummy text ever since the 1500s, when an unknown printer took a galley of type and scrambled it to make a type specimen book. It has survived not only five centuries, but also the leap into electronic typesetting, remaining essentially unchanged.</p>
  <a class="btn" href="#">Know More</a>
</section>

<section class="services">
  <h2 class="section-title display">Our <span class="accent">Services</span></h2>
  <div class="service" style="left:239px">
    <div class="icon">
      <svg width="54" height="54" viewBox="0 0 54 54" fill="none" stroke="#ff9800" stroke-width="3"><circle cx="24" cy="30" r="18"/><circle cx="24" cy="30" r="10"/><circle cx="24" cy="30" r="3" fill="#ff9800"/><path d="M24 30L46 8M40 8h6v6"/></svg>
    </div>
    <h3>Marketing Strategy</h3>
    <p>Lorem Ipsum is simply dummy text of the printing and typesetting industry. Lorem Ipsum has been the industry's</p>
    <a class="readmore" href="#">Read More...</a>
  </div>
  <div class="service" style="left:599px">
    <div class="icon filled">
      <svg width="58" height="50" viewBox="0 0 58 50" fill="none" stroke="#fff" stroke-width="3"><rect x="3" y="3" width="52" height="34"/><path d="M29 37v8M18 47h22"/><path d="M12 30V22M20 30V16M28 30V20M36 30V12M44 30V18"/><path d="M10 18l10-8 8 6 10-9 8 6"/></svg>
    </div>
    <h3>Digital Analytics</h3>
    <p>Lorem Ipsum is simply dummy text of the printing and typesetting industry. Lorem Ipsum has been the industry's</p>
    <a class="readmore" href="#">Read More...</a>
  </div>
  <div class="service" style="left:961px">
    <div class="icon">
      <svg width="58" height="58" viewBox="0 0 58 58" fill="none" stroke="#ff9800" stroke-width="3"><circle cx="20" cy="20" r="9"/><circle cx="20" cy="20" r="3"/><path d="M20 5v5M20 30v5M5 20h5M30 20h5M9 9l4 4M27 27l4 4M31 9l-4 4M9 31l4-4"/><circle cx="39" cy="39" r="10"/><circle cx="39" cy="39" r="14" stroke-dasharray="4 4"/><path d="M42 34h-4a2 2 0 0 0 0 5h2a2 2 0 0 1 0 5h-4M39 32v14"/></svg>
    </div>
    <h3>Management and Optimization</h3>
    <p>Lorem Ipsum is simply dummy text of the printing and typesetting industry. Lorem Ipsum has been the industry's</p>
    <a class="readmore" href="#">Read More...</a>
  </div>
</section>

<section class="news">
  <h2 class="section-title display">Recent <span class="accent">News</span></h2>
  <p class="intro">Lorem Ipsum is simply dummy text of the printing and typesetting industry. Lorem Ipsum has been the industry's standard dummy text ever since the 1500s,</p>
  <article class="post" style="left:78px">
    <div class="thumb" role="img" aria-label="Group of colleagues working together at a desk with a monitor" style="background:linear-gradient(135deg,#8a7768,#c9bfb6 55%,#e6e2de)">
      <div class="date"><b>24</b><span>Apr</span></div>
    </div>
    <h3>Lorem Ipsum is simply dummy text</h3>
    <p>Lorem Ipsum is simply dummy text of the printing and typesetting industry. Lorem Ipsum has been the</p>
    <a class="readmore" href="#">Read more...»</a>
  </article>
  <article class="post" style="left:439px">
    <div class="thumb" role="img" aria-label="Hands typing on a laptop on a wooden table" style="background:linear-gradient(135deg,#7a4a2c,#b57a4f 50%,#d8d6d2)">
      <div class="date"><b>24</b><span>Apr</span></div>
    </div>
    <h3>Lorem Ipsum is simply dummy text</h3>
    <p>Lorem Ipsum is simply dummy text of the printing and typesetting industry. Lorem Ipsum has been the</p>
    <a class="readmore" href="#">Read more...»</a>
  </article>
  <article class="post" style="left:801px">
    <div class="thumb" role="img" aria-label="Two colleagues reviewing work on a laptop in an office" style="background:linear-gradient(135deg,#cfd3d6,#9aa7b3 50%,#d9c7bd)">
      <div class="date"><b>24</b><span>Apr</span></div>
    </div>
    <h3>Lorem Ipsum is simply dummy text</h3>
    <p>Lorem Ipsum is simply dummy text of the printing and typesetting industry. Lorem Ipsum has been the</p>
    <a class="readmore" href="#">Read more...»</a>
  </article>
</section>

<section class="newsletter">
  <h2 class="display">Subscribe To Our Newsletter</h2>
  <div class="field">Enter E-mail*<span class="submit">SIGN IN</span></div>
</section>

<section class="testimonial">
  <h2 class="display">What Our<br><span class="accent">Client say</span></h2>
  <div class="rule"></div>
  <div class="avatar" role="img" aria-label="Portrait photo of a client"></div>
  <blockquote>Lorem Ipsum is simply dummy text of the printing and typesetting industry. Lorem Ipsum has been the industry's standard dummy text ever since the 1500s, when an unknown printer took a and scrambled it to make a type specimen book.</blockquote>
  <cite>- Client Name</cite>
  <div class="dots"><i></i><i class="on"></i><i></i><i></i><i></i></div>
</section>

<section class="contact-strip">
  <div class="contact-item" style="left:78px">
    <svg width="20" height="24" viewBox="0 0 20 24"><path fill="#ff9800" d="M10 0a9 9 0 0 0-9 9c0 7 9 15 9 15s9-8 9-15a9 9 0 0 0-9-9zm0 12.5A3.5 3.5 0 1 1 10 5.5a3.5 3.5 0 0 1 0 7z"/></svg>
    <h4>Address</h4>
    <p>123,Lorem Ipsum is simply dummy<br>text of the printing and</p>
  </div>
  <div class="contact-item" style="left:439px">
    <svg width="20" height="20" viewBox="0 0 24 24"><path fill="#ff9800" d="M6.6 10.8a15.1 15.1 0 0 0 6.6 6.6l2.2-2.2c.3-.3.7-.4 1-.2 1.1.4 2.3.6 3.6.6.6 0 1 .4 1 1V20c0 .6-.4 1-1 1A17 17 0 0 1 3 4c0-.6.4-1 1-1h3.5c.6 0 1 .4 1 1 0 1.3.2 2.5.6 3.6.1.3 0 .7-.2 1z"/></svg>
    <h4>Call Us</h4>
    <p>123 456 7890</p>
  </div>
  <div class="contact-item" style="left:801px">
    <svg width="22" height="16" viewBox="0 0 20 15"><rect width="20" height="15" fill="#ff9800"/><path d="M1 1l9 7 9-7" stroke="#fff" stroke-width="1.6" fill="none"/></svg>
    <h4>E-mail</h4>
    <p>hello@corvessa-partners.com</p>
  </div>
</section>

<footer class="site-footer">
  <div class="footer-links">
    <a href="#">Home</a><span>|</span><a href="#">About us</a><span>|</span><a href="#">Services</a><span>|</span><a href="#">News</a><span>|</span><a href="#">Contact Us</a>
  </div>
  <div class="social"><i></i><i></i><i></i></div>
  <hr>
  <p class="copyright">©BRELVANTO LLC - 2018. All Rights Reserved.</p>
</footer>

</body>
</html>
```